London Whisky Bottle Label

BACKGROUND
We are plumbers that have resurrected London's oldest once illicit Gin Distillery Harlow Post Wire https://www.vidtrove-example.net/clip/kq83pz
Bought 150yr old derelict bakery & turned it into an office for our plumbing biz....removed dangerous chimney...got sued by a neighbour ..
our lawyers discovered that the original bakers family once made illict gin here (in what is now our office) we tracked down the origianl family ...see pic enclosed....the little boy now in his 90's (Colin Treadle) gave us his family's secret gin recipe and we have now resurrected it. We supply Ravensmoor Hall, Hse of Wardens Pelling Drue etc. Now have our 1st London Whisky.
This is NOT scotch whisky...this a brand new category of drink 'English Whisky'
1. traditional whisky style bottle which will have embossed text on as per the sample English Whisky & K T Distillery LONDON
Front label 110mm x 95mm
Rear label 70mm wide and 100mm
Front Text TBC
Rear Text TBC
Must have a old map of my area London Q7 2XZ on rear
Map link https://charts.oldsheet-example.org/view/558210#zoom=6

Target Market(s)

OVER 30's

Font styles to use
Sans Serif

Requirements
Nice to have
• I want an old map on the front of the label....the map have 2 small rivers on it which are very close to my distillery (called The Hollin Race and Catter Beck, where they meet there a small bridge called Gravewick Bridge, i would like this shown on the map, is there any tasteful way to add some colour to the historic map ???

```html
<!DOCTYPE html>
<html lang="en">
<head>
<meta charset="utf-8">
<title>Ashgrove English Whisky – Labels</title>
<link rel="stylesheet" href="https://fonts.googleapis.com/css2?family=Libre+Baskerville:wght@400;700&display=swap">
<style>
  :root {
    --page: #ffffff;
    --label: #d6ccc7;
    --label-deep: #cdc3be;
    --wine: #7c1f1c;
    --gold: #d2b04c;
    --gold-soft: #e6cf7a;
    --ink: #2c2422;
    --map-light: #ece6d6;
    --map-dark: #cfc6b0;
  }
  * { box-sizing: border-box; margin: 0; padding: 0; }
  html, body { width: 1200px; height: 1200px; overflow: hidden; background: var(--page); }
  body { position: relative; font-family: "Libre Baskerville", Georgia, serif; color: var(--wine); }

  .label { position: absolute; background: linear-gradient(180deg, var(--label), var(--label-deep)); }
  .label-frame { position: absolute; inset: 0; width: 100%; height: 100%; }

  /* Front label */
  .label--front { left: 80px; top: 400px; width: 470px; height: 420px; }
  .front-ornament {
    position: absolute; left: 175px; top: 48px; width: 120px; height: 44px;
    background: radial-gradient(ellipse at center, var(--gold-soft) 0%, var(--gold) 45%, transparent 72%);
    opacity: .75;
  }
  .front-brand {
    position: absolute; left: 52px; top: 104px; width: 366px; height: 150px;
    display: flex; align-items: center; justify-content: center;
    font-size: 58px; font-weight: 700; letter-spacing: 1px; color: var(--wine);
  }
  .front-title {
    position: absolute; left: 0; right: 0; top: 282px; text-align: center;
    font-size: 32px; font-weight: 400; letter-spacing: 0.5px; line-height: 1.2; color: var(--wine);
  }
  .front-maker {
    position: absolute; left: 0; right: 0; top: 336px; text-align: center;
    font-size: 13px; letter-spacing: 4px; line-height: 1.2; color: var(--wine);
  }

  /* Rear label */
  .label--rear { left: 700px; top: 370px; width: 350px; height: 480px; }
  .rear-brand {
    position: absolute; left: 0; right: 0; top: 30px; text-align: center;
    font-size: 40px; font-weight: 700; line-height: 1.2; color: var(--wine);
  }
  .rear-intro {
    position: absolute; left: 20px; right: 20px; top: 98px; text-align: center;
    font-size: 9px; line-height: 1.4; color: var(--ink);
  }
  .rear-map {
    position: absolute; left: 24px; right: 24px; top: 162px; height: 196px;
    background: linear-gradient(160deg, var(--map-light), var(--map-dark));
  }
  .rear-volume {
    position: absolute; left: 0; right: 0; top: 376px; text-align: center;
    font-size: 10px; line-height: 1.2; color: var(--ink);
  }
  .rear-note {
    position: absolute; left: 0; right: 0; top: 396px; text-align: center;
    font-size: 9px; line-height: 1.45; color: var(--ink);
  }
</style>
</head>
<body>

<section class="label label--front" aria-label="Front label">
  <svg class="label-frame" viewBox="0 0 470 420" aria-hidden="true">
    <g fill="none" stroke="var(--gold)">
      <line x1="0" y1="4" x2="470" y2="4" stroke-width="3"/>
      <line x1="0" y1="16" x2="470" y2="16" stroke-width="1.5"/>
      <line x1="0" y1="404" x2="470" y2="404" stroke-width="1.5"/>
      <line x1="0" y1="416" x2="470" y2="416" stroke-width="3"/>
      <path d="M24 28 H446 Q446 40 456 40 V356 Q446 356 446 368 H24 Q24 356 14 356 V40 Q24 40 24 28 Z" stroke-width="1.5"/>
      <path d="M62 104 H408 V112 H418 V246 H408 V254 H62 V246 H52 V112 H62 Z" stroke-width="1.2"/>
    </g>
  </svg>
  <div class="front-ornament" role="img" aria-label="Gold crown and scroll ornament"></div>
  <div class="front-brand">Ashgrove</div>
  <h1 class="front-title">ENGLISH WHISKY</h1>
  <p class="front-maker">K T DISTILLERY LONDON</p>
</section>

<section class="label label--rear" aria-label="Rear label">
  <svg class="label-frame" viewBox="0 0 350 480" aria-hidden="true">
    <path d="M14 2 H336 Q336 14 346 14 V466 Q336 466 336 478 H14 Q14 466 4 466 V14 Q14 14 14 2 Z"
          fill="none" stroke="var(--gold)" stroke-width="2"/>
  </svg>
  <div class="rear-brand">Ashgrove</div>
  <p class="rear-intro">Lorem ipsum dolor sit amet, consectetuer adipiscing elit, sed diam nonummy nibh euismod tincidunt ut laoreet dolore magna aliquam erat volutpat. Ut wisi enim ad minim veniam, quis</p>
  <div class="rear-map" role="img" aria-label="Historic map of the Q7 2XZ area showing The Hollin Race, Catter Beck and Gravewick Bridge"></div>
  <p class="rear-volume">800 ML</p>
  <p class="rear-note">Lorem ipsum dolor sit amet,<br>consectetuer adipiscing<br>elit, sed diam nonummy<br>nibh euismod</p>
</section>

</body>
</html>
```